Halverstone Minerals Web Design

Require a Web page design for an international mining and private investment company currently based in Dubai, UAE. I would like to view designs that incorporate our current corporate logo design aimed at communicating global business development/expansion across a diversity of commodities within the mining and investment sectors.

We are a global organisation with global experience and strategy with specific business development focus in Africa, Central and South America.

Target Market(s)

Mining industry, finance, fund raising, brokering, private equity and public stock exchanges.

Industry/Entity Type

Mining

Number of Pages Required

5+ page

Font styles to use
Sans Serif

Colors

Designer to choose colors to be used in the design.

Requirements
Must have
• Corporate logo, description of who we are, what we do, corporate mission, vision & strategy.
Nice to have
• Inclusion of images, photos, interactive maps/graphics and video.

```html
<!DOCTYPE html>
<html lang="en">
<head>
<meta charset="utf-8">
<title>Halverstone Minerals</title>
<link rel="stylesheet" href="https://fonts.googleapis.com/css2?family=Poppins:ital,wght@0,400;0,500;0,600;0,700;1,400&display=swap">
<style>
:root{
  --orange:#f39c12;
  --orange-deep:#e8920c;
  --ink:#1c1c1c;
  --body:#3a3a3a;
  --white:#ffffff;
  --mist:#eef0f3;
  --footer:#141414;
  --footer-bar:#0b0b0b;
}
*{margin:0;padding:0;box-sizing:border-box}
html,body{width:1200px;height:2773px;overflow:hidden}
body{font-family:'Poppins',sans-serif;color:var(--body);background:var(--white);position:relative}
.abs{position:absolute}

/* hero */
.hero{position:absolute;left:0;top:0;width:1200px;height:642px;
  background:linear-gradient(180deg,#0d141b 0%,#1f3240 45%,#2c4450 65%,#1a2229 100%)}
.brand{left:133px;top:26px;display:flex;align-items:center;gap:10px}
.brand-mark{width:34px;height:34px;border:3px solid var(--orange);border-radius:50%}
.brand-name{font-size:17px;font-weight:600;color:var(--orange);letter-spacing:.5px;text-transform:uppercase}
.nav{left:457px;top:34px;display:flex;gap:23px;font-size:14px;font-weight:500;color:var(--white)}
.nav .active{color:var(--orange)}
.hero-title{left:0;top:245px;width:1200px;text-align:center;color:var(--white);font-size:41px;font-weight:600;line-height:53px}
.dots{left:567px;top:572px;display:flex;gap:8px}
.dots span{width:18px;height:4px;background:var(--white)}
.dots span.on{background:var(--orange)}

/* section heading with frame */
.sec-title{font-size:31px;font-weight:600;color:var(--ink);position:absolute}
.sec-title::before{content:"";position:absolute;left:-1px;top:-5px;width:44px;height:42px;border:2px solid var(--orange);border-right:none;border-bottom-width:2px}
.sec-title span{position:relative;left:18px}

/* who we are */
.who-title{left:133px;top:694px}
.who-lead{left:133px;top:758px;width:410px;font-size:13.5px;font-style:italic;line-height:23px;color:var(--body)}
.who-text{left:133px;top:806px;width:410px;font-size:13.5px;line-height:23px}
.btn{left:133px;top:939px;width:113px;height:35px;border-radius:18px;background:var(--orange);color:var(--white);font-size:11.5px;font-weight:600;text-align:center;line-height:35px;text-transform:uppercase}
.who-accent{left:764px;top:682px;width:255px;height:300px}
.who-photo{left:616px;top:697px;width:390px;height:268px;background:linear-gradient(160deg,#4a4d50,#2a2c2e 60%,#6b5a2a)}

/* mission band */
.band{left:0;top:1058px;width:1200px;height:394px}
.band-photo{left:0;top:1058px;width:640px;height:394px;background:linear-gradient(120deg,#b86e5a 0%,#3f5f86 35%,#1f3557 70%,#5c7ea6 100%)}
.band-panel{left:450px;top:1082px;width:750px;height:351px}
.mv-head{font-size:21px;font-weight:600;color:var(--orange)}
.mv-text{font-size:13.5px;line-height:23px;width:450px;margin-top:12px}
.mission{left:586px;top:1138px}
.vision{left:553px;top:1271px}

/* what we do */
.do-bg{left:0;top:1452px;width:1200px;height:591px;background:linear-gradient(180deg,#f4f5f7,#e9ebee)}
.do-title{left:133px;top:1560px}
.card{position:absolute;top:1640px;width:286px;height:192px;display:flex;flex-direction:column;align-items:center;justify-content:center;color:var(--white);font-size:22px;font-weight:600}
.card small{font-size:15px;font-weight:600;margin-top:18px}
.card-dark1{left:139px;background:linear-gradient(180deg,#4c5a66,#2c2c26)}
.card-orange{left:457px;background:var(--orange)}
.card-dark2{left:773px;background:linear-gradient(180deg,#3a3b3c,#5a4a2a)}
.card-text{position:absolute;top:1852px;width:286px;text-align:center;font-size:13.5px;line-height:23px}

/* news */
.news-title{left:493px;top:2090px}
.news{position:absolute;top:2172px;width:490px;height:191px}
.news-photo{position:absolute;left:0;top:0;width:202px;height:191px;border:2px solid #e2e2e2}
.news-photo.a{background:linear-gradient(150deg,#5a3a2a,#2a2624 60%,#7a4c34)}
.news-photo.b{background:linear-gradient(150deg,#8a8680,#4a5560 55%,#e38a2a)}
.news-body{position:absolute;left:221px;top:0;width:260px}
.news-head{font-size:15px;font-weight:500;color:var(--orange)}
.news-date{font-size:12.5px;margin-top:8px;color:var(--ink)}
.news-text{font-size:13.5px;line-height:24px;margin-top:10px}
.news-more{font-size:14px;font-weight:500;color:var(--orange);margin-top:8px}

/* footer */
.footer{left:0;top:2459px;width:1200px;height:255px;background:var(--footer)}
.f-col{position:absolute;top:2502px;color:var(--white)}
.f-head{font-size:15px;font-weight:600;text-transform:uppercase;margin-bottom:22px}
.f-text{font-size:12.5px;line-height:23px}
.f-list{list-style:none;font-size:12.5px;line-height:22.5px}
.f-row{display:flex;align-items:flex-start;gap:14px;font-size:12.5px;line-height:22px;margin-bottom:18px}
.f-row svg{flex:none;margin-top:4px}
.socials{display:flex;gap:14px;margin-top:18px}
.socials span{width:10px;height:10px;border:1.5px solid var(--white);border-radius:50%}
.sub{display:flex;margin-top:16px}
.sub-input{width:182px;height:37px;background:var(--white);font-size:10.5px;font-style:italic;color:#888;line-height:37px;padding-left:10px}
.sub-btn{width:40px;height:37px;background:var(--orange);display:flex;align-items:center;justify-content:center}
.f-bar{left:0;top:2714px;width:1200px;height:59px;background:var(--footer-bar);color:var(--white);font-size:12.5px;text-align:center;line-height:59px}
</style>
</head>
<body>

<header class="hero" role="img" aria-label="Night view of an industrial refinery and oil pumpjacks">
</header>
<div class="abs brand"><span class="brand-mark"></span><span class="brand-name">Halverstone Minerals</span></div>
<nav class="abs nav">
  <span class="active">Home</span><span>Who We Are</span><span>What We Do</span><span>Corporate Mission</span><span>Vision &amp; Strategy</span><span>Contact us</span>
</nav>
<h1 class="abs hero-title">We are an International Mining and<br>Private Investment Company</h1>
<div class="abs dots"><span class="on"></span><span></span><span></span></div>

<section>
  <h2 class="sec-title who-title"><span>Who We Are</span></h2>
  <p class="abs who-lead">Sed ut perspiciatis unde omnis iste natus error sit voluptatem accusantium doloremque laudantium</p>
  <p class="abs who-text">But I must explain to you how all this mistaken idea of denouncing pleasure and praising pain was born and I will give you a complete account of the system, and expound the actual teachings of the great explorer of the truth, the master-builder of human happiness.</p>
  <div class="abs btn">Read More</div>
  <svg class="abs who-accent" viewBox="0 0 255 300" aria-hidden="true"><polygon points="0,300 255,300 255,0 40,0 40,270 0,300" fill="var(--orange)"/></svg>
  <div class="abs who-photo" role="img" aria-label="Wheel loader filling a dump truck in an open-pit mine"></div>
</section>

<section>
  <div class="abs band-photo" role="img" aria-label="Stacks of coins over a stock market ticker board"></div>
  <svg class="abs band-panel" viewBox="0 0 750 351" aria-hidden="true"><polygon points="85,0 750,0 750,351 0,351" fill="#fff"/></svg>
  <div class="abs mission"><h3 class="mv-head">Our Mission</h3><p class="mv-text">But I must explain to you how all this mistaken idea of denouncing pleasure and praising pain was born and I will give you a complete account of the system, and expound.</p></div>
  <div class="abs vision"><h3 class="mv-head">Our Vision</h3><p class="mv-text">But I must explain to you how all this mistaken idea of denouncing pleasure and praising pain was born and I will give you a complete account of the system, and expound.</p></div>
</section>

<section>
  <div class="abs do-bg" role="img" aria-label="Faded background of mining trucks at a site"></div>
  <h2 class="sec-title do-title"><span>What We Do</span></h2>
  <div class="card card-dark1" role="img" aria-label="Mining excavator at an ore heap">Mine Operations</div>
  <div class="card card-orange">Quality Control<small>See More</small></div>
  <div class="card card-dark2" role="img" aria-label="Yellow dump trucks at a quarry">Dump Truck</div>
  <p class="card-text" style="left:139px">At vero eos et accusamus et iusto odio dignissimos ducimus qui blanditiis praesentium voluptatum deleniti atque corrupti quos dolores et quas molestias</p>
  <p class="card-text" style="left:457px">At vero eos et accusamus et iusto odio dignissimos ducimus qui blanditiis praesentium voluptatum deleniti atque corrupti quos dolores et quas molestias</p>
  <p class="card-text" style="left:773px">At vero eos et accusamus et iusto odio dignissimos ducimus qui blanditiis praesentium voluptatum deleniti atque corrupti quos dolores et quas molestias</p>
</section>

<section>
  <h2 class="sec-title news-title"><span>Latest News</span></h2>
  <article class="news" style="left:128px">
    <div class="news-photo a" role="img" aria-label="Bucket wheel of a mining excavator"></div>
    <div class="news-body">
      <h4 class="news-head">Nemo enim ipsam voluptatem</h4>
      <p class="news-date">18 May 2018</p>
      <p class="news-text">Lorem ipsum dolor sit amet, consectetur adipiscing elit, sed do eiusmod tempor incididunt ut labore et dolore magna aliqua. Ut</p>
      <p class="news-more">Read More</p>
    </div>
  </article>
  <article class="news" style="left:623px">
    <div class="news-photo b" role="img" aria-label="Mine worker in safety gear inside a tunnel"></div>
    <div class="news-body">
      <h4 class="news-head">Nemo enim ipsam voluptatem</h4>
      <p class="news-date">18 May 2018</p>
      <p class="news-text">Lorem ipsum dolor sit amet, consectetur adipiscing elit, sed do eiusmod tempor incididunt ut labore et dolore magna aliqua. Ut</p>
      <p class="news-more">Read More</p>
    </div>
  </article>
</section>

<footer>
  <div class="abs footer"></div>
  <div class="f-col" style="left:140px;width:230px">
    <h5 class="f-head">About Us</h5>
    <p class="f-text">Lorem ipsum dolor sit amet, consectetur adipiscing elit, sed do eiusmod tempor incididunt ut labore et dolore magna aliqua.</p>
    <div class="socials"><span></span><span></span><span></span><span></span></div>
  </div>
  <div class="f-col" style="left:423px">
    <h5 class="f-head">Links</h5>
    <ul class="f-list"><li>Home</li><li>Who We Are</li><li>What We Do</li><li>Corporate Mission</li><li>Vision &amp; Strategy</li><li>Contact us</li></ul>
  </div>
  <div class="f-col" style="left:582px;width:240px">
    <h5 class="f-head">Contact Us</h5>
    <div class="f-row"><svg width="14" height="16" viewBox="0 0 14 16"><path d="M7 1a5 5 0 0 1 5 5c0 4-5 9-5 9S2 10 2 6a5 5 0 0 1 5-5z" fill="none" stroke="#fff" stroke-width="1.3"/><circle cx="7" cy="6" r="1.8" fill="none" stroke="#fff" stroke-width="1.2"/></svg><span># 24, Quarry Lane,<br>Ridgeview RV 2048</span></div>
    <div class="f-row"><svg width="14" height="14" viewBox="0 0 14 14"><path d="M3 1l2.5 3-1.5 1.5c.8 1.8 2.2 3.2 4 4L9.5 8 13 10.5 11.5 13C6 13 1 8 1 2.5z" fill="#fff"/></svg><span>+1 5550142870</span></div>
    <div class="f-row"><svg width="15" height="11" viewBox="0 0 15 11"><rect x="0" y="0" width="15" height="11" fill="#fff"/><path d="M0 0l7.5 6L15 0" fill="none" stroke="#141414" stroke-width="1.2"/></svg><span>info@halverstoneminerals.com</span></div>
  </div>
  <div class="f-col" style="left:841px;width:230px">
    <h5 class="f-head">Newsletter</h5>
    <p class="f-text">But I must explain to you how all this mistaken idea of denouncing pleasure and praising.</p>
    <div class="sub"><div class="sub-input">Enter your email address</div><div class="sub-btn"><svg width="14" height="12" viewBox="0 0 14 12"><path d="M0 6h12M7 1l5 5-5 5" fill="none" stroke="#fff" stroke-width="2"/></svg></div></div>
  </div>
  <div class="abs f-bar">© 2018 Halverstone Minerals | All Rights Reserved</div>
</footer>

</body>
</html>
```